NEW Modern Sleek Business Card for VR Language Startup

Our startup is using VR to lead the next wave of world language education. We need a two-sided business card that introduces the larger organization (Brightloom Language Inc) and our contact info on one side and shows the product, Glimwoorld, on the other side.

Side 1 (contact info)= Brightloom Logo and Contact info (name, title, phone, email)

Side 2 (product)= Glimworld logo, text, and website
Text= Culturally Immersive Language Learning Games
Website= www.glimworld-play.com

Target Market(s)

Education, Technology

Contact Information for Business Card

Contact info will be updated upon approval of the design. For now, put this as a placeholder.

Perry Dunmore
Founder & CEO
pdunmore@quillpost-mail.net
(555)-014-2286

Font styles to use
Other font styles liked:
• Gibson and Century Gothic are the brand fonts

Requirements
Nice to have
• I would love to see cohesion between the design and colors of the two logos. I have attached a few business card designs that I like, so you can get a feel for my preferred style.

```html
<!DOCTYPE html>
<html lang="en">
<head>
<meta charset="utf-8">
<title>Brightloom Language · Glimworld Business Card</title>
<link rel="stylesheet" href="https://fonts.googleapis.com/css2?family=Montserrat:wght@400;500;600;700&display=swap">
<style>
  :root {
    --backdrop: #d9dbe0;
    --card: #ffffff;
    --ink: #2b2b2e;
    --ink-soft: #55565b;
    --rule: #3a3a3e;
    --sky: #37b6ee;
    --indigo: #5a6fd0;
    --violet: #8a4fc4;
    --magenta: #e0357e;
    --orange: #f58a2c;
  }
  * { box-sizing: border-box; margin: 0; padding: 0; }
  html, body { width: 1200px; height: 900px; overflow: hidden; }
  body {
    background: var(--backdrop);
    font-family: "Montserrat", "Century Gothic", sans-serif;
    color: var(--ink);
    position: relative;
  }
  .card {
    position: absolute;
    width: 620px;
    height: 354px;
    background: var(--card);
    box-shadow: 0 6px 18px rgba(0,0,0,.18);
    overflow: hidden;
  }
  .card--product { left: 120px; top: 60px; }
  .card--contact { left: 460px; top: 486px; }

  .corner-accent {
    position: absolute;
    left: 0; top: 0;
    width: 200px; height: 150px;
    border-bottom-right-radius: 100% 100%;
  }
  .card--product .corner-accent {
    background: radial-gradient(circle at 0 0, rgba(55,182,238,.35), rgba(90,111,208,.12) 70%, rgba(255,255,255,0) 100%);
  }
  .card--contact .corner-accent {
    background: radial-gradient(circle at 0 0, rgba(138,79,196,.32), rgba(224,53,126,.12) 70%, rgba(255,255,255,0) 100%);
  }

  .brand {
    position: absolute;
    display: flex;
    align-items: center;
    gap: 16px;
  }
  .brand__dot { width: 62px; height: 62px; border-radius: 50%; }
  .brand__name { font-weight: 600; letter-spacing: .5px; }

  .card--product .brand { right: 52px; top: 74px; }
  .card--product .brand__dot { background: linear-gradient(135deg, var(--sky), var(--indigo)); }
  .card--product .brand__name { font-size: 40px; color: var(--indigo); }

  .card--contact .brand { right: 58px; top: 64px; }
  .card--contact .brand__dot { background: linear-gradient(135deg, var(--orange), var(--magenta), var(--sky)); }
  .card--contact .brand__name { font-size: 36px; color: var(--ink); letter-spacing: 2px; }

  .rule { position: absolute; height: 1.5px; background: var(--rule); }
  .card--product .rule--top { left: 320px; right: 52px; top: 160px; }
  .card--product .rule--mid { left: 50px; right: 200px; top: 236px; }

  .website {
    position: absolute; left: 50px; top: 206px;
    font-size: 19px; font-weight: 600;
    background: linear-gradient(90deg, var(--sky), var(--indigo));
    -webkit-background-clip: text; background-clip: text; color: transparent;
  }
  .tagline {
    position: absolute; left: 50px; top: 252px;
    font-size: 18px; font-weight: 500; line-height: 1.3;
    color: var(--ink-soft);
  }

  .card--contact .rule--top { left: 300px; right: 58px; top: 156px; }
  .card--contact .rule--mid { left: 50px; right: 250px; top: 258px; }

  .person {
    position: absolute; left: 50px; top: 186px;
  }
  .person__name {
    font-size: 26px; font-weight: 700; letter-spacing: .5px; text-transform: uppercase;
    background: linear-gradient(90deg, var(--orange), var(--magenta) 45%, var(--violet) 70%, var(--sky));
    -webkit-background-clip: text; background-clip: text; color: transparent;
  }
  .person__role { font-size: 19px; font-weight: 600; color: var(--ink); margin-top: 2px; }

  .contact-list {
    position: absolute; left: 50px; top: 276px;
    list-style: none;
    font-size: 20px; font-weight: 500; color: var(--ink);
  }
  .contact-list li { display: flex; align-items: center; gap: 14px; line-height: 1.45; }
  .contact-list svg { width: 20px; height: 20px; flex: none; }
</style>
</head>
<body>

<section class="card card--product" aria-label="Glimworld product side">
  <div class="corner-accent" role="img" aria-label="Decorative corner accent in blue tones"></div>
  <div class="brand">
    <span class="brand__dot"></span>
    <span class="brand__name">Glimworld</span>
  </div>
  <div class="rule rule--top"></div>
  <p class="website">www.glimworld-play.com</p>
  <div class="rule rule--mid"></div>
  <p class="tagline">Culturally Immersive<br>Language Learning Games</p>
</section>

<section class="card card--contact" aria-label="Brightloom Language contact side">
  <div class="corner-accent" role="img" aria-label="Decorative corner accent in violet and pink tones"></div>
  <div class="brand">
    <span class="brand__dot"></span>
    <span class="brand__name">Brightloom</span>
  </div>
  <div class="rule rule--top"></div>
  <div class="person">
    <p class="person__name">Perry Dunmore</p>
    <p class="person__role">Founder &amp; CEO</p>
  </div>
  <div class="rule rule--mid"></div>
  <ul class="contact-list">
    <li>
      <svg viewBox="0 0 24 24" aria-hidden="true">
        <defs><linearGradient id="icon-grad" x1="0" y1="0" x2="1" y2="1">
          <stop offset="0" stop-color="#f58a2c"/><stop offset="1" stop-color="#e0357e"/></linearGradient></defs>
        <path fill="url(#icon-grad)" d="M6.6 10.8a15.1 15.1 0 0 0 6.6 6.6l2.2-2.2a1 1 0 0 1 1-.25 11.4 11.4 0 0 0 3.6.57 1 1 0 0 1 1 1V20a1 1 0 0 1-1 1A17 17 0 0 1 3 4a1 1 0 0 1 1-1h3.5a1 1 0 0 1 1 1c0 1.25.2 2.45.57 3.6a1 1 0 0 1-.25 1z"/>
      </svg>
      (555)-014-2286
    </li>
    <li>
      <svg viewBox="0 0 24 24" aria-hidden="true">
        <rect x="2" y="5" width="20" height="14" rx="1.5" fill="url(#icon-grad)"/>
        <path d="M3 6.5l9 6.5 9-6.5" fill="none" stroke="#fff" stroke-width="1.6"/>
      </svg>
      pdunmore@quillpost-mail.net
    </li>
  </ul>
</section>

</body>
</html>
```